Corvane Freight Company Business Card Design

We are a company that delivers natural saltwater (from the ocean) to aquarium companies, restaurants and home marine tanks. I would like a new business card to suit.

Must include Name, company name, abn, contact number and website as well as logo (see attached).

Looking for a design that stands out, has a clean but unique appearance.

Double and single sided entries welcome

Business

• Logo

```html
<!DOCTYPE html>
<html lang="en">
<head>
<meta charset="utf-8">
<title>Corvane Freight Company – Business Card</title>
<link href="https://fonts.googleapis.com/css2?family=Open+Sans:wght@400;600;700;800&display=swap" rel="stylesheet">
<style>
  :root {
    --backdrop: #1c1c1c;
    --card-blue: #1a5fae;
    --name-plate: #3b7cc6;
    --ink-white: #ffffff;
    --ink-soft: #e6eef8;
  }
  * { margin: 0; padding: 0; box-sizing: border-box; }
  html, body {
    width: 1200px;
    height: 405px;
    overflow: hidden;
    background: var(--backdrop);
    font-family: "Open Sans", Arial, sans-serif;
  }
  .canvas { position: relative; width: 1200px; height: 405px; }
  .card {
    position: absolute;
    top: 49px;
    width: 531px;
    height: 302px;
    background: var(--card-blue);
    border-radius: 18px;
    color: var(--ink-white);
  }
  .card--front { left: 49px; }
  .card--back { left: 621px; }

  .brand-name {
    position: absolute;
    font-weight: 800;
    color: var(--ink-white);
    letter-spacing: -0.5px;
    line-height: 1;
    white-space: nowrap;
  }
  .card--front .brand-name { left: 36px; top: 70px; font-size: 38px; }
  .card--back .brand-name { left: 0; right: 0; top: 118px; font-size: 40px; text-align: center; }

  .contact-list {
    position: absolute;
    left: 36px;
    top: 173px;
    list-style: none;
    font-size: 13px;
    line-height: 20px;
    color: var(--ink-soft);
  }
  .contact-list li { display: flex; align-items: center; gap: 5px; }
  .contact-list svg { width: 11px; height: 11px; flex: none; }

  .address {
    position: absolute;
    left: 36px;
    top: 245px;
    font-size: 13px;
    line-height: 19px;
    font-style: normal;
    color: var(--ink-soft);
  }
  .address strong { display: block; font-weight: 700; color: var(--ink-white); }

  .name-plate {
    position: absolute;
    left: 327px;
    top: 167px;
    width: 180px;
    height: 76px;
    border-radius: 50%;
    background: var(--name-plate);
    text-align: center;
    padding-top: 24px;
  }
  .name-plate .person { font-size: 16px; font-weight: 700; line-height: 18px; }
  .name-plate .role { font-size: 12px; line-height: 17px; color: var(--ink-soft); }

  .web-address {
    position: absolute;
    left: 0; right: 0;
    top: 238px;
    text-align: center;
    font-size: 15px;
    letter-spacing: 3px;
    color: var(--ink-white);
  }
</style>
</head>
<body>
<main class="canvas">
  <section class="card card--front" aria-label="Card front">
    <div class="brand-name">Corvane Freight</div>

    <ul class="contact-list">
      <li>
        <svg viewBox="0 0 12 12" aria-hidden="true"><path fill="#fff" d="M2.4 1 4 .9l1 2.6-1.2.9a6 6 0 0 0 3.8 3.8l.9-1.2 2.6 1-.1 1.6c-.1.6-.6 1-1.2 1A9 9 0 0 1 1.4 2.2c0-.6.4-1.1 1-1.2z"/></svg>
        123-456-7890
      </li>
      <li>
        <svg viewBox="0 0 12 12" aria-hidden="true"><circle cx="6" cy="6" r="5.5" fill="#fff"/><path d="M.5 6h11M6 .5c-2.5 3-2.5 8 0 11M6 .5c2.5 3 2.5 8 0 11" stroke="#1a5fae" stroke-width=".9" fill="none"/></svg>
        www.website.com
      </li>
      <li>ABN : 0123456789</li>
    </ul>

    <address class="address">
      <strong>Corvane Freight.LLC</strong>
      Street Name, City Name, State, City Zip Code
    </address>

    <div class="name-plate">
      <div class="person">Your name</div>
      <div class="role">Title</div>
    </div>
  </section>

  <section class="card card--back" aria-label="Card back">
    <div class="brand-name">Corvane Freight</div>
    <div class="web-address">www.website.com</div>
  </section>
</main>
</body>
</html>
```